Book Cover for a book on Quiet Ventures

I am self-publishing my book on Brindlecart and need a book cover made. Below are the details. See attached templates for size we need to use. I also attached a previous cover we had made that I liked. The problem with it was they were two boys helping each other but the book is about women. I'm open to your ideas on the cover though, but I wanted to show you a style I liked as an idea.
Front of Cover
Book Title: Quiet Ventures
Book Subtitle: Raw Reflections of a Female CEO
Author Name: Lorna T. Pelham
Add on the Spine of Cover: Quiet Ventures and Lorna T. Pelham
Back of the Cover Text:
Quiet Ventures: Unvarnished Notes of a Woman Founder is an honest account of a business owner’s experience attempting to navigate the start-up community while also pursuing spiritual growth. Author Lorna Pelham defines a spiritual entrepreneur as “someone who runs an enterprise with the purpose of growing love rather than material gain.” This book discusses the three dimensions of Quiet Ventures:
1. The business is an integral part of the founder’s spiritual journey.
2. Employees working for the spiritual enterprise, whether they know it or not, encounter this company because it's part of their spiritual path.
3. The business itself has a life force of its own and its purpose is to further the kingdom of heaven on earth.
These three dimensions happen simultaneously and work together to produce the greatest possible result. However, this can feel confusing to a founder juggling these dimensions while also trying to manage and run a business. This is not a formulaic self-help book or roadmap. Rather, it is a compilation of personal reflections that often seem at odds with the traditional world of entrepreneurship.
Below the description add my picture (see attached for my picture)
Bio text:
Lorna Pelham founded Halvex with the vision of ushering in a life-long education system that shifts away from standardization to one that empowers people to live their purpose. In college, Lorna interned for Open Meadow, a women’s empowerment initiative where she recognized her passion for helping people find their voice. Lorna's 20-year journey has come full circle to empowering other female CEOs who are pursuing the path of Quiet Ventures.
NOTE: Please note that Brindlecart puts a bar code on the bottom right of the back cover as is noted on the attached template.
Size template is attached to the brief, here are the sizes typed out:
# Description Width (in) Height (in)
1 Full Cover 12.79 9.25
2 Front Cover 6 9
3 Safe Area 5.875 8.75
4 Bleed 0.125 0.125
5 Margin 0.125 0.125
6 Spine 0.54 9
7 Spine Safe Area 0.415 8.75
8 Spine Margin 0.062 0.062
9 Barcode Margin 0.25 0.25
Pre-publication checklist
BRINDLECART TIPS for the final cover:
1. Save as a PDF. Your cover must be a single PDF that includes the back cover, spine, and front cover as one image.
2. Flatten all transparencies. These can cause the file to print with missing or distorted content. Consult your software's documentation to learn how.
3. Embed your fonts. Consult your software's documentation to learn how.
4. Remove crop marks, color bars, template text. Crop marks are lines showing where pages should be trimmed. Color bars are strips with a series of patches used to ensure color balance during printing. Also, remove any template text, PDF creation guides, or software references.
5. Ensure your cover image meets the minimum resolution of 300 DPI (dots per inch).
6. Optimize PDFs. Optimization is useful to reduce your file size, allowing for higher performance when transferring, uploading, viewing, and printing the files.
7. Remove file security. Locked or encrypted files will fail review.
Target Market(s)
Women who want to be CEOs or are currently CEOs of companies.
Industry/Entity Type
Entrepreneurship, business, spirituality
Requirements
Must have
- Just the text on the description. A very welcoming feel.
Nice to have
- I like the idea of having a sunrise/sunset in the image somehow like in the example I attached to the brief, but again I'm open.
Should not have
- Please don't put any yoga or meditation poses or hands outstretched. I have a lot of interesting ones that look like my example so if you are going to submit after Saturday 10/29, please only do so if you have a new idea! Thanks!

```html
<!DOCTYPE html>
<html lang="en">
<head>
<meta charset="UTF-8">
<title>Quiet Ventures – Book Cover</title>
<link rel="stylesheet" href="https://fonts.googleapis.com/css2?family=Noto+Serif:ital,wght@0,400;0,500;1,400&display=swap">
<style>
  :root {
    --navy-deep: #020b1f;
    --navy-mid: #0b2a52;
    --navy-glow: #15406e;
    --gold: #f4d21f;
    --ink-light: #ffffff;
    --photo-teal: #1f4a44;
    --photo-olive: #5c6b3a;
    --photo-warm: #8a6a48;
  }
  * { margin: 0; padding: 0; box-sizing: border-box; }
  html, body { width: 1200px; height: 874px; overflow: hidden; background: var(--navy-deep); }
  .cover {
    position: relative;
    width: 1200px;
    height: 874px;
    font-family: "Noto Serif", Georgia, serif;
    color: var(--ink-light);
    background: var(--navy-deep);
    overflow: hidden;
  }

  /* Back panel */
  .back {
    position: absolute;
    left: 0; top: 0;
    width: 636px; height: 874px;
    background: radial-gradient(ellipse 420px 520px at 300px 470px, var(--navy-glow) 0%, var(--navy-mid) 40%, var(--navy-deep) 100%);
  }
  .blurb {
    position: absolute;
    left: 37px; top: 59px;
    width: 501px;
    font-size: 12.8px;
    line-height: 16.9px;
    letter-spacing: 0.06em;
    text-align: justify;
    hyphens: auto;
  }
  .blurb p { margin-bottom: 16.9px; }
  .blurb .lead { color: var(--gold); }
  .blurb ol { list-style: none; }
  .blurb li { padding-left: 46px; margin-bottom: 16.9px; }

  .author-photo {
    position: absolute;
    left: 37px; top: 485px;
    width: 124px; height: 124px;
    background: linear-gradient(180deg, #f4f1ee 0%, #e9d9d3 55%, #e2307f 100%);
  }
  .bio {
    position: absolute;
    left: 184px; top: 481px;
    width: 363px;
    font-size: 12.8px;
    line-height: 16.9px;
    letter-spacing: 0.06em;
    text-align: justify;
    hyphens: auto;
  }

  /* Spine */
  .spine-title {
    position: absolute;
    left: 572px; top: 100px;
    height: 400px;
    writing-mode: vertical-rl;
    text-align: center;
  }
  .spine-title .main {
    display: block;
    color: var(--gold);
    font-size: 23px;
    letter-spacing: 0.04em;
    line-height: 28px;
  }
  .spine-title .sub {
    display: block;
    font-style: italic;
    font-size: 17px;
    letter-spacing: 0.03em;
    line-height: 26px;
  }
  .spine-author {
    position: absolute;
    left: 587px; top: 600px;
    height: 200px;
    writing-mode: vertical-rl;
    text-align: center;
    font-size: 21px;
    letter-spacing: 0.1em;
  }

  /* Front panel */
  .front {
    position: absolute;
    left: 636px; top: 0;
    width: 564px; height: 874px;
    background: var(--navy-deep);
  }
  .hero {
    position: absolute;
    left: 0; top: 0;
    width: 564px; height: 570px;
    background:
      linear-gradient(180deg, rgba(2,11,31,0) 55%, var(--navy-deep) 100%),
      radial-gradient(ellipse 220px 260px at 280px 230px, var(--photo-warm) 0%, rgba(138,106,72,0) 100%),
      linear-gradient(100deg, var(--photo-olive) 0%, var(--photo-teal) 55%, #27404a 100%);
  }
  .front-title {
    position: absolute;
    left: 0; top: 572px;
    width: 564px;
    text-align: center;
    color: var(--gold);
    font-weight: 400;
    font-size: 44px;
    line-height: 52px;
    letter-spacing: 0.06em;
  }
  .front-subtitle {
    position: absolute;
    left: 0; top: 670px;
    width: 564px;
    text-align: center;
    font-style: italic;
    font-size: 26px;
    letter-spacing: 0.03em;
    white-space: nowrap;
  }
  .front-author {
    position: absolute;
    left: 0; top: 806px;
    width: 564px;
    text-align: center;
    font-size: 31px;
    letter-spacing: 0.1em;
  }
</style>
</head>
<body>
<main class="cover">
  <section class="back">
    <div class="blurb">
      <p><span class="lead">QUIET VENTURES:</span> Unvarnished Notes of a Woman Founder is an honest account of a business owner’s experience attempting to navigate the start-up community while also pursuing spiritual growth. Author Lorna Pelham defines a spiritual entrepreneur as “someone who runs an enterprise with the purpose of growing love rather than material gain.” This book discusses the three dimensions of Quiet Ventures:</p>
      <ol>
        <li>1. The business is an integral part of the founder’s spiritual journey.</li>
        <li>2. Employees working for the spiritual enterprise, whether they know it or not, encounter this company because it's part of their spiritual path.</li>
        <li>3. The business itself has a life force of its own and its purpose is to further the kingdom of heaven on earth.</li>
      </ol>
      <p>These three dimensions happen simultaneously and work together to produce the greatest possible result. However, this can feel confusing to a founder juggling these dimensions while also trying to manage and run a business. This is not a formulaic self-help book or roadmap. Rather, it is a compilation of personal reflections that often seem at odds with the traditional world of entrepreneurship.</p>
    </div>
    <div class="author-photo" role="img" aria-label="Portrait photo of the author, Lorna Pelham"></div>
    <p class="bio">Lorna Pelham founded Halvex with the vision of ushering in a life-long education system that shifts away from standardization to one that empowers people to live their purpose. In college, Lorna interned for Open Meadow, a women’s empowerment initiative where she recognized her passion for helping people find their voice. Lorna's 20-year journey has come full circle to empowering other female CEOs who are pursuing the path of Quiet Ventures.</p>

    <div class="spine-title">
      <span class="main">QUIET VENTURES</span>
      <span class="sub">Unvarnished Notes of a Woman Founder</span>
    </div>
    <div class="spine-author">Lorna T. Pelham</div>
  </section>

  <section class="front">
    <div class="hero" role="img" aria-label="Photo of a smiling woman at her desk with a laptop and a mug, warm window light behind her"></div>
    <h1 class="front-title">QUIET<br>VENTURES</h1>
    <p class="front-subtitle">Unvarnished Notes of a Woman Founder</p>
    <p class="front-author">Lorna T. Pelham</p>
  </section>
</main>
</body>
</html>
```